Brenlow Estates Website and Logo Design

We need a new logo and website designed for 'Brenlow Estates Ltd', which is a well established Guernsey property holding company founded in 1934.

The company does not currently have a website. The new website should be similar in style and layout to https://www.quorvanhall.example/.

Target Market(s)

Industry, Media, Tenants

Industry/Entity Type

Property Management

Logo Text

BEL OR Brenlow Estates Ltd OR BE

Coding

Coded - Design and coding required

Number of Pages Required

4 page

Font styles to use
Other font styles liked:
• Helvetica

Requirements
Must have
• The logo laying over the picture (like https://www.quorvanhall.example/).
• Big pictures on homepage (like https://www.quorvanhall.example/)

```html
<!DOCTYPE html>
<html lang="en">
<head>
<meta charset="utf-8">
<title>Brenlow Estates Ltd</title>
<link href="https://fonts.googleapis.com/css2?family=Lato:wght@400;700&family=Open+Sans:wght@400;600&family=Roboto+Condensed:wght@700&display=swap" rel="stylesheet">
<style>
:root{
  --teal:#1ec8c8;
  --teal-dark:#14b3b3;
  --black:#000;
  --ink:#111;
  --grey-text:#666;
  --grey-band:#e4e4e4;
  --mint:#c8f1f0;
  --white:#fff;
}
*{margin:0;padding:0;box-sizing:border-box}
html,body{width:1200px;height:4358px;overflow:hidden}
body{position:relative;background:var(--white);font-family:"Open Sans",Arial,sans-serif;color:var(--ink)}
.abs{position:absolute}
.teal{color:var(--teal)}
.btn{position:absolute;display:flex;align-items:center;justify-content:center;background:var(--teal);color:var(--white);font-family:"Open Sans",Arial,sans-serif;font-size:17px;text-transform:uppercase;border-radius:4px}
.heading{position:absolute;left:0;width:1200px;text-align:center;font-family:Lato,Arial,sans-serif;font-size:41px;font-weight:400}

/* header */
.site-header{position:absolute;top:0;left:0;width:1200px;height:190px;background:var(--black)}
.brand{position:absolute;left:80px;top:22px;display:flex;flex-direction:column;align-items:center;gap:8px}
.brand-mark{width:74px;height:74px;border:3px solid var(--teal);border-radius:50%}
.brand-name{font-family:"Open Sans",Arial,sans-serif;font-size:22px;font-weight:600;color:var(--teal);text-align:center;line-height:1.1;width:160px}
.social{position:absolute;top:13px;left:452px;display:flex;gap:14px}
.social span{width:36px;height:36px;border-radius:50%;background:var(--teal)}
.help{position:absolute;top:18px;left:793px;color:var(--white);font-size:19px}
.phone{position:absolute;top:14px;left:964px;display:flex;align-items:center;gap:12px;color:var(--white);font-size:19px}
.main-nav{position:absolute;top:96px;left:474px;display:flex;align-items:center}
.main-nav a{color:var(--white);text-decoration:none;font-size:19px;padding:0 14px;height:50px;display:flex;align-items:center}
.main-nav a.active{background:var(--teal);padding:0 26px;margin-right:14px}

/* hero */
.hero{position:absolute;top:190px;left:0;width:1200px;height:914px;background:var(--black)}
.hero svg{position:absolute;top:0;left:0}
.hero-title{position:absolute;top:108px;left:0;width:1200px;text-align:center;font-family:"Roboto Condensed",Arial,sans-serif;font-weight:700;font-size:86px;color:var(--white);letter-spacing:2px}
.hero-tag{position:absolute;top:224px;left:418px;width:364px;height:56px;background:#d2d2d2;font-family:"Roboto Condensed",Arial,sans-serif;font-weight:700;font-size:32px;color:#222;display:flex;align-items:center;justify-content:center}
.hero-cta{position:absolute;top:296px;left:494px;width:212px;height:66px;border-radius:33px;background:var(--black);color:var(--white);font-size:19px;display:flex;align-items:center;justify-content:center}
.era{position:absolute;width:280px;text-align:center;font-family:"Open Sans",Arial,sans-serif;font-size:25px;color:var(--teal);letter-spacing:1px}

/* welcome */
.welcome{position:absolute;top:1104px;left:0;width:1200px;height:419px;background:var(--grey-band)}
.welcome p{position:absolute;top:125px;left:196px;width:808px;text-align:center;font-size:15.5px;line-height:26px;color:#333}
.welcome .btn{top:314px;left:510px;width:180px;height:54px;background:var(--black);border:5px solid var(--teal);border-radius:2px;font-size:20px}

/* about */
.about{position:absolute;top:1523px;left:0;width:1200px;height:491px}
.about .heading{left:78px;width:auto;text-align:left;top:56px}
.about p{position:absolute;top:130px;left:78px;width:600px;font-size:15.5px;line-height:29px;color:var(--grey-text)}
.about .photo{position:absolute;top:125px;left:709px;width:363px;height:255px}
.about .btn{top:366px;left:78px;width:166px;height:62px;border-radius:0}

/* services */
.services{position:absolute;top:2014px;left:0;width:1200px;height:572px;background:var(--black)}
.services .heading{top:46px;color:var(--white)}
.card{position:absolute;top:131px;width:245px;height:360px;background:var(--white);border-radius:6px;text-align:center}
.card h3{margin-top:10px;font-family:"Open Sans",Arial,sans-serif;font-weight:400;font-size:21px;color:var(--teal)}
.card .icon{width:134px;height:134px;border-radius:50%;background:var(--teal);margin:12px auto 0;display:flex;align-items:center;justify-content:center}
.card p{margin:26px auto 0;width:190px;font-size:14px;line-height:19px;color:#555}
.card .btn{position:relative;margin:20px auto 0;width:176px;height:56px;border-radius:28px;font-size:17px}
.card.featured{background:var(--teal)}
.card.featured h3{color:var(--ink)}
.card.featured .icon{background:var(--white)}
.card.featured p{color:var(--white)}
.card.featured .btn{background:var(--white);color:var(--ink)}
.dots{position:absolute;top:540px;left:548px;display:flex;gap:14px}
.dots span{width:16px;height:16px;border-radius:50%;background:var(--white)}
.dots span:first-child{background:var(--teal)}

/* projects */
.projects{position:absolute;top:2586px;left:0;width:1200px;height:587px}
.projects .heading{top:64px}
.project{position:absolute;top:157px;width:322px;text-align:center}
.project .photo{width:322px;height:215px}
.project h4{margin-top:12px;font-weight:400;font-size:20px;color:#777}
.project p{margin-top:4px;font-size:15.5px;line-height:21px;color:#666}
.project .btn{position:relative;margin:17px auto 0;width:152px;height:50px;border-radius:25px}

/* testimonial */
.testimonial{position:absolute;top:3173px;left:0;width:1200px;height:364px;background:var(--mint)}
.testimonial .heading{top:34px}
.client-name{position:absolute;top:116px;left:184px;font-family:Lato,Arial,sans-serif;font-size:23px;color:var(--teal-dark)}
.client-role{position:absolute;top:151px;left:184px;font-size:15px;color:#222}
.client-rule{position:absolute;top:178px;left:184px;width:690px;height:1px;background:#9bb}
.quote{position:absolute;top:196px;left:196px;width:690px;font-size:16.5px;line-height:29px;color:#222}
.qmark{position:absolute;font-family:Georgia,serif;font-size:44px;font-weight:700;color:#222;line-height:1}
.client-photo{position:absolute;top:103px;left:868px;width:138px;height:138px;border-radius:50%;border:4px solid var(--white);background:linear-gradient(160deg,#d9d4cf,#8a7d75)}
.arrow{position:absolute;top:130px}

/* news */
.news{position:absolute;top:3537px;left:0;width:1200px;height:531px}
.news .heading{top:64px}
.post{position:absolute;top:139px;width:335px}
.post .photo{width:335px;height:189px;position:relative}
.date{position:absolute;top:0;left:0;width:56px;height:74px;background:var(--black);color:var(--white);text-align:center;font-family:Lato,Arial,sans-serif}
.date b{display:block;font-size:29px;font-weight:400;margin-top:6px}
.date small{font-size:12px}
.date.hot{background:var(--teal)}
.post h4{margin-top:50px;font-weight:400;font-size:18px;color:#111}
.post h4.hot{color:var(--teal)}
.post p{margin-top:6px;font-size:14.5px;line-height:20px;color:#666}
.post .more{margin-top:14px;font-size:14px;color:#111;text-transform:uppercase;display:flex;align-items:center;gap:6px}
.post .more.hot{color:var(--teal)}

/* footer */
.site-footer{position:absolute;top:4068px;left:0;width:1200px;height:290px;background:var(--teal);color:var(--white)}
.footer-nav{position:absolute;top:60px;left:78px;display:flex;gap:34px;font-size:21px}
.footer-rule{position:absolute;top:121px;left:78px;width:1044px;height:1px;background:rgba(255,255,255,.6)}
.footer-icons{position:absolute;top:171px;left:410px;display:flex;gap:62px}
.footer-icons span{width:34px;height:34px;border-radius:50%;border:3px solid var(--white)}
.copyright{position:absolute;top:234px;left:0;width:1200px;text-align:center;font-size:15px;font-weight:600}
</style>
</head>
<body>

<header class="site-header">
  <div class="brand">
    <span class="brand-mark"></span>
    <span class="brand-name">Brenlow Estates Ltd</span>
  </div>
  <div class="social"><span></span><span></span><span></span><span></span></div>
  <div class="help">How can we help</div>
  <div class="phone">
    <svg width="38" height="38" viewBox="0 0 38 38"><circle cx="19" cy="19" r="19" fill="#1ec8c8"/><path d="M13 10c1-1 2-1 3 0l2 3c.6 1 .4 2-.4 2.6l-1.2 1c1 2.3 2.8 4.2 5 5.2l1-1.2c.7-.8 1.7-1 2.6-.4l3 2c1 1 1 2 0 3l-1.4 1.4c-1.6 1.6-5 .6-8.7-3.1S10 14 11.6 12.4z" fill="#fff"/></svg>
    <span>555-014-2290</span>
  </div>
  <nav class="main-nav">
    <a class="active">HOME</a><a>ABOUT</a><a>SERVICES</a><a>PROJECTS</a><a>NEWS</a><a>CONTACT</a>
  </nav>
</header>

<section class="hero">
  <svg width="1200" height="914" viewBox="0 0 1200 914">
    <defs>
      <linearGradient id="harbour" x1="0" y1="0" x2="0" y2="1">
        <stop offset="0" stop-color="#8d8a84"/>
        <stop offset=".45" stop-color="#6f6b64"/>
        <stop offset="1" stop-color="#3e4b52"/>
      </linearGradient>
      <linearGradient id="fields" x1="0" y1="0" x2="0" y2="1"><stop offset="0" stop-color="#c9d6e0"/><stop offset=".4" stop-color="#7e9a62"/><stop offset="1" stop-color="#5c6f48"/></linearGradient>
      <linearGradient id="boats" x1="0" y1="0" x2="0" y2="1"><stop offset="0" stop-color="#6e9a52"/><stop offset=".55" stop-color="#9a7a5c"/><stop offset="1" stop-color="#3d6f86"/></linearGradient>
      <linearGradient id="town" x1="0" y1="0" x2="0" y2="1"><stop offset="0" stop-color="#8fb6d9"/><stop offset=".5" stop-color="#c9a46c"/><stop offset="1" stop-color="#3c6b8f"/></linearGradient>
    </defs>
    <path d="M0 0H1200V320Q600 800 0 320Z" fill="url(#harbour)" role="img" aria-label="Photograph of a harbour town with moored boats and hillside houses"/>
    <path d="M0 320Q600 800 1200 320" fill="none" stroke="#1ec8c8" stroke-width="14"/>
    <circle cx="221" cy="598" r="140" fill="url(#fields)" stroke="#1ec8c8" stroke-width="11" role="img" aria-label="Photograph of green island fields by the coast"/>
    <circle cx="607" cy="612" r="140" fill="url(#boats)" stroke="#1ec8c8" stroke-width="11" role="img" aria-label="Photograph of small boats on a shore under trees"/>
    <circle cx="973" cy="598" r="140" fill="url(#town)" stroke="#1ec8c8" stroke-width="11" role="img" aria-label="Photograph of a waterfront town with a church spire"/>
  </svg>
  <div class="hero-title">BRENLOW</div>
  <div class="hero-tag">Estates Business Ltd</div>
  <div class="hero-cta">CONTACT NOW</div>
  <div class="era" style="top:760px;left:87px">YESTERDAY</div>
  <div class="era" style="top:780px;left:467px">TODAY</div>
  <div class="era" style="top:780px;left:833px">TOMORROW</div>
</section>

<section class="welcome">
  <h2 class="heading" style="top:56px">Welcome to <span class="teal">Brenlow Estates</span></h2>
  <p>Brenlow Estates Limited (BEL) is a family-owned Guernsey property holding company. It purchases properties that are considered to have potential for development either through refurbishment or by obtaining planning permission to change its classification from, for example, industrial premises to offices or retail outlets, or by the marriage value of buying an adjacent property to one already owned by BEL. BEL's reputation as a fair-minded landlord stems from the application of the founder's tenet of working with the tenant to help maximise the business benefits of both parties.</p>
  <div class="btn">READ MORE</div>
</section>

<section class="about">
  <h2 class="heading">About <span class="teal">Brenlow Estates</span></h2>
  <p>The Bailiwick of Guernsey is a British Crown dependency in the English Channel. The benefit of establishing a company in Guernsey is the island's low tax jurisdiction since there are no capital taxes and no corporation taxes for many companies. Consequently since the 1980s the island's development as an ideal financial centre for the establishment of institutions and banks has thrived. There are currently more than 160 companies registered with the Island Financial Standards Board.</p>
  <div class="photo" role="img" aria-label="Photograph of small boats moored in a calm bay" style="background:linear-gradient(180deg,#a9c4dc 0%,#8fb0c9 40%,#2f5f86 60%,#24506f 100%)"></div>
  <div class="btn">READ MORE</div>
</section>

<section class="services">
  <h2 class="heading"><span class="teal">Brenlow Estates</span>&nbsp;&nbsp;Services</h2>
  <div class="card featured" style="left:78px">
    <h3>Lorem Ipsum</h3>
    <div class="icon"><svg width="54" height="54" viewBox="0 0 54 54"><path d="M10 50V16l16-6v40zM28 50V20l16 5v25z" fill="#111"/><path d="M14 20h3v3h-3zM20 20h3v3h-3zM14 28h3v3h-3zM20 28h3v3h-3zM14 36h3v3h-3zM20 36h3v3h-3zM32 28h3v3h-3zM38 28h3v3h-3zM32 36h3v3h-3zM38 36h3v3h-3z" fill="#fff"/></svg></div>
    <p>Lorem Ipsum is simply dummy text of the printing and typesetting industry</p>
    <div class="btn">READ MORE</div>
  </div>
  <div class="card" style="left:343px">
    <h3>Lorem Ipsum</h3>
    <div class="icon"><svg width="60" height="60" viewBox="0 0 60 60" fill="#fff"><circle cx="19" cy="12" r="7"/><circle cx="41" cy="12" r="7"/><path d="M10 24h18v14h-4v16h-10V38h-4zM32 24h18v14h-4v16H36V38h-4z"/><rect x="24" y="30" width="12" height="4"/></svg></div>
    <p>Lorem Ipsum is simply dummy text of the printing and typesetting industry</p>
    <div class="btn">READ MORE</div>
  </div>
  <div class="card" style="left:616px">
    <h3>Lorem Ipsum</h3>
    <div class="icon"><svg width="60" height="60" viewBox="0 0 60 60" fill="#fff"><circle cx="30" cy="18" r="14"/><text x="30" y="25" text-anchor="middle" font-family="Arial,sans-serif" font-size="20" font-weight="700" fill="#1ec8c8">$</text><path d="M6 44h12l10 4h10v4H24v2h16l14-8v4L40 58H6z"/></svg></div>
    <p>Lorem Ipsum is simply dummy text of the printing and typesetting industry</p>
    <div class="btn">READ MORE</div>
  </div>
  <div class="card" style="left:880px">
    <h3>Lorem Ipsum</h3>
    <div class="icon"><svg width="60" height="60" viewBox="0 0 60 60" fill="none" stroke="#fff" stroke-width="5" stroke-linecap="round"><path d="M16 22a16 16 0 0 1 26-6"/><path d="M44 38a16 16 0 0 1-26 6"/><path d="M42 8v9h-9M18 52v-9h9"/><circle cx="30" cy="30" r="5" fill="#fff"/></svg></div>
    <p>Lorem Ipsum is simply dummy text of the printing and typesetting industry</p>
    <div class="btn">READ MORE</div>
  </div>
  <div class="dots"><span></span><span></span><span></span><span></span></div>
</section>

<section class="projects">
  <h2 class="heading">Brenlow Estates <span class="teal">Projects</span></h2>
  <div class="project" style="left:78px">
    <div class="photo" role="img" aria-label="Photograph of a rocky islet with boats in a bay" style="background:linear-gradient(180deg,#9fc0de 0%,#b7cfe2 40%,#6c7e70 52%,#2f6a94 62%,#24587e 100%)"></div>
    <h4>Project Title</h4>
    <p>Lorem Ipsum is simply dummy text of the printing and typesetting industry.</p>
    <div class="btn">READ MORE</div>
  </div>
  <div class="project" style="left:439px">
    <div class="photo" role="img" aria-label="Photograph of a marina full of yachts below a town" style="background:linear-gradient(180deg,#a7b9cc 0%,#c3c7c4 35%,#8d8a80 55%,#c9d0d6 75%,#3c6a8c 100%)"></div>
    <h4>Project Title</h4>
    <p>Lorem Ipsum is simply dummy text of the printing and typesetting industry.</p>
    <div class="btn">READ MORE</div>
  </div>
  <div class="project" style="left:802px">
    <div class="photo" role="img" aria-label="Photograph of a harbour wall with a waterfront town" style="background:linear-gradient(180deg,#4d86c6 0%,#9fbfe0 38%,#8b7d68 55%,#2d5f86 70%,#1f4d72 100%)"></div>
    <h4>Project Title</h4>
    <p>Lorem Ipsum is simply dummy text of the printing and typesetting industry.</p>
    <div class="btn">READ MORE</div>
  </div>
</section>

<section class="testimonial">
  <h2 class="heading">What <span class="teal">Client Say</span></h2>
  <svg class="arrow" style="left:78px" width="40" height="64" viewBox="0 0 40 64"><path d="M34 6 8 32l26 26" fill="none" stroke="#1ec8c8" stroke-width="8"/></svg>
  <svg class="arrow" style="left:1086px" width="40" height="64" viewBox="0 0 40 64"><path d="M6 6l26 26-26 26" fill="none" stroke="#111" stroke-width="8"/></svg>
  <div class="client-name">Mara Ellison</div>
  <div class="client-role">CEO AND FOUNDER</div>
  <div class="client-rule"></div>
  <div class="qmark" style="top:196px;left:154px">&ldquo;</div>
  <p class="quote">Lorem Ipsum is simply dummy text of the printing and typesetting industry. Lorem Ipsum has been the industry's standard dummy text ever since the 1500s, when an unknown printer took a galley of type and scrambled it to make a type specimen book.</p>
  <div class="qmark" style="top:276px;left:828px">&rdquo;</div>
  <div class="client-photo" role="img" aria-label="Portrait photograph of the client"></div>
</section>

<section class="news">
  <h2 class="heading">Latest <span class="teal">News</span></h2>
  <article class="post" style="left:78px">
    <div class="photo" role="img" aria-label="Photograph of a marina with flower baskets on a railing" style="background:linear-gradient(180deg,#8fb3d6 0%,#b9c6cf 40%,#5f7f95 60%,#b24b5a 85%,#6b8a4a 100%)"><div class="date hot"><b>14</b><small>MAY</small></div></div>
    <h4 class="hot">Lorem Ipsum is simply text Dummy</h4>
    <p>Lorem Ipsum is simply dummy text of the printing and typesetting industry.</p>
    <div class="more hot">READ MORE <span>&raquo;</span></div>
  </article>
  <article class="post" style="left:433px">
    <div class="photo" role="img" aria-label="Photograph of a sunlit harbour with boats against the light" style="background:linear-gradient(180deg,#56738f 0%,#c9d3da 40%,#8ea2b2 55%,#3a4a56 100%)"><div class="date"><b>26</b><small>JAN</small></div></div>
    <h4>Lorem Ipsum is simply text Dummy</h4>
    <p>Lorem Ipsum is simply dummy text of the printing and typesetting industry.</p>
    <div class="more">READ MORE <span>&raquo;</span></div>
  </article>
  <article class="post" style="left:788px">
    <div class="photo" role="img" aria-label="Photograph of a ferry moored at a quay" style="background:linear-gradient(180deg,#7aa3cc 0%,#d6dde3 45%,#9aa4ad 65%,#3d5d78 100%)"><div class="date"><b>15</b><small>SEP</small></div></div>
    <h4>Lorem Ipsum is simply text Dummy</h4>
    <p>Lorem Ipsum is simply dummy text of the printing and typesetting industry.</p>
    <div class="more">READ MORE <span>&raquo;</span></div>
  </article>
</section>

<footer class="site-footer">
  <nav class="footer-nav"><span>Home</span><span>Services</span><span>Specials</span><span>Financing</span><span>Customer Referral Program</span><span>Contact us</span></nav>
  <div class="footer-rule"></div>
  <div class="footer-icons"><span></span><span></span><span></span><span></span><span></span></div>
  <div class="copyright">&copy; Holloway Climate Services - 2016. All Rights Reserved</div>
</footer>

</body>
</html>
```